Duct Manufacturing Company new to the industry needs business card and stationary design

we are sheet metal duct manufacturers looking for a business card design to fit my new business logo.
nothing to crazy that will date, but want it to stand out from the crowed.
I'm sure you guys will work it out.

Contact Information for Business Card

Glen Marsh
Director

Address
17 Dorwell St
Tarrawong NSW 2684

0438 760 514

Sales@flowbend.com.au

Font styles to use
Other font styles liked:
• BankGothic md bt

Requirements
Nice to have
• Like the idea of corner rounded to match logo
• like to keep colours flowing
• font I like sharp square not rounded

```html
<!DOCTYPE html>
<html lang="en">
<head>
<meta charset="utf-8">
<title>Flowbend Industries – Business Card</title>
<link href="https://fonts.googleapis.com/css2?family=Michroma&family=Montserrat:wght@400;500&display=swap" rel="stylesheet">
<style>
  :root {
    --backdrop: #a3a3a5;
    --card-white: #fbfbfb;
    --brand-blue: #1c63b0;
    --blue-top: #1b80c8;
    --blue-bottom: #1a4590;
    --brand-green: #7cc242;
    --green-deep: #2aa146;
    --text-white: #ffffff;
  }
  * { margin: 0; padding: 0; box-sizing: border-box; }
  html, body { width: 1200px; height: 1200px; overflow: hidden; }
  body { background: var(--backdrop); position: relative; font-family: "Montserrat", sans-serif; }

  .card {
    position: absolute;
    width: 713px;
    height: 419px;
    border-radius: 22px;
    background: var(--card-white);
    overflow: hidden;
  }
  .card--front { left: 238px; top: 118px; }
  .card--back { left: 230px; top: 643px; }

  .card__stripe { position: absolute; left: 0; bottom: 0; width: 100%; height: 17px; }
  .card__panel { position: absolute; inset: 0; width: 100%; height: 100%; }

  .brand-name {
    position: absolute;
    text-align: center;
    font-family: "Michroma", sans-serif;
    color: var(--brand-blue);
    line-height: 1.05;
  }
  .card--front .brand-name { left: 0; right: 0; top: 245px; font-size: 34px; }
  .card--front .brand-name span { display: block; font-size: 25px; letter-spacing: 3px; }
  .card--back .brand-name { left: 20px; width: 300px; top: 240px; font-size: 29px; }
  .card--back .brand-name span { display: block; font-size: 21px; letter-spacing: 3px; }

  .contact { position: absolute; left: 402px; top: 104px; color: var(--text-white); }
  .contact__name { font-family: "Michroma", sans-serif; font-size: 21px; letter-spacing: 1.5px; }
  .contact__role { font-size: 16px; margin-top: 4px; }
  .contact__list { list-style: none; margin-top: 26px; font-size: 18px; }
  .contact__list li { display: flex; align-items: center; height: 27px; }
  .contact__list svg { width: 18px; height: 16px; margin-right: 17px; fill: var(--text-white); }
  .contact__address { font-size: 18px; margin-top: 3px; line-height: 24px; }
</style>
</head>
<body>

  <section class="card card--front" aria-label="Card front">
    <div class="brand-name">FLOWBEND<span>INDUSTRIES</span></div>
    <svg class="card__stripe" viewBox="0 0 713 17" preserveAspectRatio="none" aria-hidden="true">
      <defs>
        <linearGradient id="stripeGreen" x1="0" x2="1">
          <stop offset="0" stop-color="var(--green-deep)"/>
          <stop offset="1" stop-color="var(--brand-green)"/>
        </linearGradient>
        <linearGradient id="stripeBlue" x1="0" x2="1">
          <stop offset="0" stop-color="var(--blue-top)"/>
          <stop offset="1" stop-color="var(--blue-bottom)"/>
        </linearGradient>
      </defs>
      <rect x="0" y="0" width="713" height="17" fill="url(#stripeGreen)"/>
      <polygon points="505,0 713,0 713,17 465,17" fill="#ffffff"/>
      <polygon points="511,0 713,0 713,17 471,17" fill="url(#stripeBlue)"/>
    </svg>
  </section>

  <section class="card card--back" aria-label="Card back">
    <svg class="card__panel" viewBox="0 0 713 419" aria-hidden="true">
      <defs>
        <linearGradient id="panelBlue" x1="0" y1="0" x2="0" y2="1">
          <stop offset="0" stop-color="var(--blue-top)"/>
          <stop offset="1" stop-color="var(--blue-bottom)"/>
        </linearGradient>
      </defs>
      <path d="M266 0 L300 0 Q412 200 300 419 L292 419 Q385 190 266 0 Z" fill="var(--brand-green)"/>
      <path d="M300 0 Q412 200 300 419 L713 419 L713 0 Z" fill="url(#panelBlue)"/>
    </svg>

    <div class="brand-name">FLOWBEND<span>INDUSTRIES</span></div>

    <div class="contact">
      <div class="contact__name">GLEN MARSH</div>
      <div class="contact__role">Director</div>
      <ul class="contact__list">
        <li>
          <svg viewBox="0 0 18 16"><path d="M1 5 Q9 -1 17 5 L14 7 L12 4 L6 4 L4 7 Z"/><path d="M4 8 L14 8 L16 15 L2 15 Z"/></svg>
          0438 760 514
        </li>
        <li>
          <svg viewBox="0 0 18 16"><circle cx="9" cy="8" r="7" fill="none" stroke="#fff" stroke-width="1.6"/><ellipse cx="9" cy="8" rx="3" ry="7" fill="none" stroke="#fff" stroke-width="1.4"/><path d="M2 8 H16" stroke="#fff" stroke-width="1.4"/></svg>
          flowbend.com.au
        </li>
        <li>
          <svg viewBox="0 0 18 16"><rect x="1" y="2" width="16" height="12"/><path d="M1 2 L9 9 L17 2" fill="none" stroke="#1a5aa5" stroke-width="1.5"/></svg>
          sales@flowbend.com.au
        </li>
      </ul>
      <div class="contact__address">17 Dorwell St<br>Tarrawong NSW 2684</div>
    </div>
  </section>

</body>
</html>
```